Maple Grove Schools | brand new stationery!

We need stationery design with our new logo! Our company updated it's name and image and we like to incorporate the new one on our stationery, business cards and email signature. We are looking for fresh, new ideas!
Industry: Childcare, Elementary and Middle School
Company Name: Maple Grove Schools
Tagline: Bright Futures Start Here
Main colors: Blue, white and a little yellow
Star shape is something new for us! Do you see a way to incorporate it as a design element?

```html
<!DOCTYPE html>
<html lang="en">
<head>
<meta charset="utf-8">
<title>Maple Grove Schools – Business Cards</title>
<link rel="stylesheet" href="https://fonts.googleapis.com/css2?family=Montserrat:wght@600&family=Arimo:wght@400;700&display=swap">
<style>
  :root {
    --canvas: #2a2a2a;
    --card: #0b0b0b;
    --white: #f2f2f2;
    --yellow: #f5b700;
    --blue: #152a8c;
    --divider: #4a4a4a;
  }
  * { margin: 0; padding: 0; box-sizing: border-box; }
  html, body {
    width: 1200px; height: 900px; overflow: hidden;
    background: var(--canvas);
  }
  .stage {
    width: 1200px; height: 900px;
    display: flex; flex-direction: column;
    align-items: center; justify-content: center; gap: 50px;
  }
  .card {
    width: 620px; height: 354px;
    background: var(--card);
    position: relative;
    box-shadow: 0 12px 30px rgba(0,0,0,.5);
    color: var(--white);
  }
  .brand {
    display: flex; align-items: center; gap: 14px;
    font-family: "Montserrat", sans-serif; font-weight: 600;
    color: var(--white);
  }
  .brand-dot {
    width: 46px; height: 46px; border-radius: 50%;
    background: var(--blue); flex: none;
  }
  .brand-name { font-size: 34px; line-height: 1.05; }

  /* contact side */
  .card-contact { display: flex; align-items: center; }
  .card-contact .brand { width: 300px; justify-content: center; padding-left: 20px; }
  .card-contact .brand-name { font-size: 30px; }
  .divider {
    width: 1px; height: 200px; background: var(--divider);
  }
  .details {
    padding-left: 34px;
    font-family: "Arimo", sans-serif; font-size: 15px; line-height: 1.45;
  }
  .person-name {
    color: var(--yellow); font-weight: 700; font-size: 19px; letter-spacing: .5px;
  }
  .person-role { margin-bottom: 10px; }
  .contact-list { list-style: none; margin-bottom: 12px; }
  .contact-list li { display: flex; align-items: center; gap: 9px; }
  .contact-list svg { width: 15px; height: 15px; flex: none; }
  .highlight { color: var(--yellow); }

  /* logo side */
  .card-logo { display: flex; flex-direction: column; align-items: center; justify-content: center; gap: 22px; }
  .card-logo .brand-name { font-size: 40px; }
  .tagline {
    font-family: "Arimo", sans-serif; font-size: 17px; color: var(--yellow);
  }
</style>
</head>
<body>
<main class="stage">
  <section class="card card-logo">
    <div class="brand">
      <span class="brand-dot"></span>
      <span class="brand-name">Maple Grove<br>Schools</span>
    </div>
    <p class="tagline">Bright Futures Start Here</p>
  </section>

  <section class="card card-contact">
    <div class="brand">
      <span class="brand-dot"></span>
      <span class="brand-name">Maple Grove<br>Schools</span>
    </div>
    <div class="divider"></div>
    <div class="details">
      <p class="person-name">DANIEL HART</p>
      <p class="person-role">Managing Director</p>
      <ul class="contact-list">
        <li>
          <svg viewBox="0 0 24 24" aria-hidden="true"><path fill="#f5b700" d="M6.6 10.8a15.1 15.1 0 0 0 6.6 6.6l2.2-2.2a1 1 0 0 1 1-.25 11.4 11.4 0 0 0 3.6.57 1 1 0 0 1 1 1V20a1 1 0 0 1-1 1A17 17 0 0 1 3 4a1 1 0 0 1 1-1h3.5a1 1 0 0 1 1 1c0 1.25.2 2.45.57 3.57a1 1 0 0 1-.25 1z"/></svg>
          044-555 018 240
        </li>
        <li>
          <svg viewBox="0 0 24 24" aria-hidden="true"><rect x="2" y="5" width="20" height="14" fill="#f5b700"/><path d="M2 5l10 8 10-8" fill="none" stroke="#0b0b0b" stroke-width="2"/></svg>
          hello@maplegrove.example
        </li>
        <li>
          <svg viewBox="0 0 24 24" aria-hidden="true"><g fill="none" stroke="#f5b700" stroke-width="2"><circle cx="12" cy="12" r="9"/><ellipse cx="12" cy="12" rx="4" ry="9"/><path d="M3 12h18M5 7h14M5 17h14"/></g></svg>
          <span>www.<span class="highlight">maplegrove</span>.example</span>
        </li>
      </ul>
      <p class="address">18 Orchard Lane, Brookfield<br>20417, Westland</p>
    </div>
  </section>
</main>
</body>
</html>
```